Business Card for Coastal Tundrabridge Advisory

We need a business card for Coastal Tundrabridge Advisory. The company website address is provided below. The company logo is attached. We provide specialized permafrost services to the mining, transportation, and oil & gas industries. The card should be prepared for:
Matthias Korhonen, PhD.
Coastal Tundrabridge Advisory
PO Box 418259
Quillwater, Alaska 99642
Direct: +1-907-555-0143
Email: mkorhonen@tundrabridgeadvisory.example
Website: www.coastaltundrabridgeadvisory.example

```html
<!DOCTYPE html>
<html lang="en">
<head>
<meta charset="utf-8">
<title>Coastal Tundrabridge Advisory – Business Card</title>
<link rel="stylesheet" href="https://fonts.googleapis.com/css2?family=Montserrat:wght@400;500;700&display=swap">
<style>
  :root {
    --ink-navy: #111a24;
    --paper: #ffffff;
    --text-dark: #1b2431;
    --backdrop: #e6e4e0;
    --wordmark: #ffffff;
  }
  * { box-sizing: border-box; margin: 0; padding: 0; }
  html, body { width: 1200px; height: 931px; overflow: hidden; }
  body {
    background: var(--backdrop);
    font-family: "Montserrat", sans-serif;
    position: relative;
  }
  .card {
    position: absolute;
    width: 640px;
    height: 381px;
    border-radius: 22px;
    overflow: hidden;
    box-shadow: 0 14px 30px rgba(0,0,0,0.22);
  }
  .card--front {
    left: 190px; top: 60px;
    background: var(--ink-navy);
    display: flex; align-items: center; justify-content: center;
  }
  .card--back {
    left: 370px; top: 490px;
    background: var(--paper);
    display: flex;
  }
  .wordmark {
    color: var(--wordmark);
    font-weight: 500;
    text-transform: uppercase;
    text-align: center;
    letter-spacing: 0.18em;
    line-height: 1.35;
  }
  .card--front .wordmark { font-size: 30px; }
  .back-info {
    width: 57%;
    padding: 44px 0 36px 44px;
    display: flex; flex-direction: column;
    color: var(--text-dark);
  }
  .back-brand {
    width: 43%;
    background: var(--ink-navy);
    display: flex; align-items: center; justify-content: center;
    padding: 0 18px;
  }
  .back-brand .wordmark { font-size: 17px; letter-spacing: 0.14em; }
  .person-name { font-size: 21px; font-weight: 700; }
  .person-title { font-size: 14px; font-weight: 400; margin-top: 4px; }
  .postal { margin-top: auto; font-size: 14px; line-height: 1.4; }
  .contact-list { list-style: none; margin-top: 14px; font-size: 13px; }
  .contact-list li { display: flex; align-items: center; gap: 12px; margin-top: 7px; }
  .contact-list svg { width: 14px; height: 14px; flex: none; fill: var(--text-dark); }
</style>
</head>
<body>
  <section class="card card--front">
    <p class="wordmark">Coastal<br>Tundrabridge<br>Advisory</p>
  </section>

  <section class="card card--back">
    <div class="back-info">
      <h1 class="person-name">Matthias Korhonen, PhD.</h1>
      <p class="person-title">Managing Director</p>
      <p class="postal">PO Box 418259<br>Quillwater, Alaska 99642</p>
      <ul class="contact-list">
        <li>
          <svg viewBox="0 0 24 24" aria-hidden="true"><path d="M6.6 10.8a15.1 15.1 0 0 0 6.6 6.6l2.2-2.2a1 1 0 0 1 1-.25 11.4 11.4 0 0 0 3.6.57 1 1 0 0 1 1 1V20a1 1 0 0 1-1 1A17 17 0 0 1 3 4a1 1 0 0 1 1-1h3.5a1 1 0 0 1 1 1c0 1.25.2 2.45.57 3.57a1 1 0 0 1-.25 1z"/></svg>
          <span>+1-907-555-0143</span>
        </li>
        <li>
          <svg viewBox="0 0 24 24" aria-hidden="true"><path d="M2 5h20v14H2z M2 5l10 8 10-8" fill="none" stroke="#1b2431" stroke-width="0"/><path d="M2 5h20v2l-10 7L2 7zM2 9l10 7 10-7v10H2z"/></svg>
          <span>mkorhonen@tundrabridgeadvisory.example</span>
        </li>
        <li>
          <svg viewBox="0 0 24 24" aria-hidden="true"><circle cx="12" cy="12" r="10" fill="none" stroke="#1b2431" stroke-width="2"/><path d="M2 12h20M12 2c3 3 3 17 0 20M12 2c-3 3-3 17 0 20" fill="none" stroke="#1b2431" stroke-width="1.6"/></svg>
          <span>www.coastaltundrabridgeadvisory.example</span>
        </li>
      </ul>
    </div>
    <div class="back-brand">
      <p class="wordmark">Coastal<br>Tundrabridge<br>Advisory</p>
    </div>
  </section>
</body>
</html>
```